Sparkling Wine Label Mirren Hollow

Super Premium Sparkling Wine Label

We are a super premium tasmanian fine wine producer and are about to release our first Sparking Wine.

please visit www.mirrenhollow-example.com.au to check out our range of wine. We need a label that will sit within this branding but as the aspirational product. We think that the Vosse grey/navy label will fit into this concept. It is masculine clean elegent and very smick,
and would be a great addition to our line see Argent Pinot Noir label.

However you can be quite creative with Sparkling Line eg Belvane Royal Cuvee is a stunning classical french label featuring gold baroque detail and feminine elegence.

Its up to you if you where spending $50 on a special bottles of sparkling wine what would you expect to see?

Black/Gold Graphite/Gold

Needs a neck /collar label

Main Front Label
Mirren Hollow
Chardonnay Pinot Noir
Tasmania

Back label has all the techical into you can use the back label from existing labels but reverserve out the colours to black and white or graphite and white

We want a label that oozes quality and expense. That says this the way I want to celebrate.

Target Market(s)

40 60 age group appreciator of quality

Industry/Entity Type

Product

Requirements
Must have
• Neck label
Simular to Vosse Shield so
MIRREN arched above
G rondel in middle possibiliy replacing coat of arms
TASMANIA arched under in red

Main Front Label
Mirren Hollow
Tasmania
Chardonnay Pinot Noir 750ML

Back Label / use the attachment Mirren label just reverse out so that it is a black label with white writing and amend information
Mirren Hollow
23 Pell Morrow Rd Ashvale
Tasmania, 7261
0412557390
www.mirrenhollow-example.com.au
contact@mirrenhollow-example.com.au
Sulphur Dioxide Added
Alc/Vol 12.5%
7.7 Standard Drinks

Rondel g

```html
<!DOCTYPE html>
<html lang="en">
<head>
<meta charset="utf-8">
<title>Mirren Hollow Sparkling Label</title>
<link rel="stylesheet" href="https://fonts.googleapis.com/css2?family=Pinyon+Script&family=Tinos&family=Arimo&display=swap">
<style>
  :root {
    --ground: #ffffff;
    --edge-black: #070707;
    --copper-deep: #3e1604;
    --copper-mid: #8a3510;
    --copper-glow: #d0621c;
    --panel-light: #ead3aa;
    --panel-mid: #d2b58a;
    --panel-dark: #b3936b;
    --panel-rim: #f6e8c4;
    --ornament: #e9d6ae;
    --ink: #121212;
    --wine-red: #5e1010;
    --paper-white: #ffffff;
  }
  html, body {
    margin: 0;
    padding: 0;
    overflow: hidden;
    background: var(--ground);
  }
  .label {
    position: relative;
    width: 1200px;
    height: 1111px;
    overflow: hidden;
    background: var(--ground);
  }
  .label-shape {
    position: absolute;
    inset: 0;
  }
  .label-text {
    position: absolute;
    left: 0;
    width: 100%;
    text-align: center;
    margin: 0;
    line-height: 1;
  }
  .brand-name {
    top: 355px;
    font-family: "Pinyon Script", cursive;
    font-size: 170px;
    color: var(--ink);
  }
  .brand-sub {
    top: 540px;
    font-family: "Arimo", sans-serif;
    font-size: 44px;
    letter-spacing: 1px;
    color: #1e1e1e;
  }
  .region {
    top: 610px;
    font-family: "Tinos", serif;
    font-size: 48px;
    letter-spacing: 2px;
    color: var(--paper-white);
  }
  .varietal {
    top: 680px;
    font-family: "Pinyon Script", cursive;
    font-size: 74px;
    color: #2a1a18;
  }
  .varietal .accent {
    color: var(--wine-red);
  }
  .vintage {
    top: 868px;
    font-family: "Tinos", serif;
    font-size: 42px;
    letter-spacing: 2px;
    color: var(--paper-white);
  }
</style>
</head>
<body>
<main class="label">
  <svg class="label-shape" width="1200" height="1111" viewBox="0 0 1200 1111" xmlns="http://www.w3.org/2000/svg">
    <defs>
      <radialGradient id="copperFill" cx="50%" cy="50%" r="60%">
        <stop offset="0%" stop-color="var(--copper-glow)"/>
        <stop offset="55%" stop-color="var(--copper-mid)"/>
        <stop offset="100%" stop-color="var(--copper-deep)"/>
      </radialGradient>
      <linearGradient id="panelFill" x1="0" y1="0" x2="1" y2="0">
        <stop offset="0%" stop-color="var(--panel-mid)"/>
        <stop offset="45%" stop-color="var(--panel-light)"/>
        <stop offset="100%" stop-color="var(--panel-dark)"/>
      </linearGradient>
      <path id="outerOutline" d="M600,2 Q760,10 850,100 Q1000,90 1110,200 Q1200,300 1150,380 Q1200,470 1198,555 Q1200,640 1150,730 Q1200,810 1110,910 Q1000,1020 850,1010 Q760,1100 600,1108 Q440,1100 350,1010 Q200,1020 90,910 Q0,810 50,730 Q0,640 2,555 Q0,470 50,380 Q0,300 90,200 Q200,90 350,100 Q440,10 600,2Z"/>
    </defs>

    <use class="label-edge" href="#outerOutline" fill="var(--edge-black)"/>
    <g class="glitter-border" role="img" aria-label="Sparkling copper glitter border">
      <use href="#outerOutline" fill="url(#copperFill)" transform="translate(600 555) scale(0.955) translate(-600 -555)"/>
    </g>

    <path class="cartouche" fill="url(#panelFill)" stroke="var(--panel-rim)" stroke-width="4"
      d="M600,125 C700,125 760,150 800,200 C900,195 1000,230 1040,330 C1060,400 1090,440 1090,555 C1090,670 1060,710 1040,780 C1000,880 900,915 800,910 C760,955 700,968 600,968 C500,968 440,955 400,910 C300,915 200,880 160,780 C140,710 110,670 110,555 C110,440 140,400 160,330 C200,230 300,195 400,200 C440,150 500,125 600,125Z"/>

    <rect class="ornament ornament-crest" role="img" aria-label="Gold embossed scrollwork crest" x="425" y="195" width="350" height="70" rx="35" fill="var(--ornament)" opacity="0.55"/>
    <rect class="ornament ornament-side-left" role="img" aria-label="Gold filigree flourish" x="145" y="415" width="140" height="285" rx="60" fill="var(--ornament)" opacity="0.5"/>
    <rect class="ornament ornament-side-right" role="img" aria-label="Gold filigree flourish" x="915" y="415" width="140" height="285" rx="60" fill="var(--ornament)" opacity="0.5"/>
    <rect class="ornament ornament-base" role="img" aria-label="Gold filigree flourish" x="535" y="825" width="130" height="60" rx="30" fill="var(--ornament)" opacity="0.5"/>
  </svg>

  <h1 class="label-text brand-name">Mirren</h1>
  <p class="label-text brand-sub">HOLLOW</p>
  <p class="label-text region">TASMANIA</p>
  <p class="label-text varietal">Chardonnay <span class="accent">Pinot</span> Noir</p>
  <p class="label-text vintage">2011</p>
</main>
</body>
</html>
```